Business card design for new eCommerce site focusing on integrity and strong businsess tactics

We need a business card that will stand out and be memorable. Something with color that matches our company logo colors. Think high end version of Pactivo. There are 2 logos provided. The parent company is called Amber Ledge Partners and we are presenting a new and very exciting eCommerce site called BrightHarborTrade.example.

Target Market(s)

Our target markets are in the Activities, Food and Beverage, Health and Beauty

Industry/Entity Type

Marketing

Contact Information for Business Card

We have 4 members that need cards...I will provide all info to the winner of the design contest
Business Address is
4870 West 63rd Avenue, Suite C207
Phoenix AZ 85731

Font styles to use
Serif
Sans Serif

Colors

Designer to choose colors to be used in the design.

Requirements
Must have
• The card must be memorable...should be unique in design but must exude integrity and be playful .
• I have provided several colors or our parent company...please feel free to use which ever
Nice to have
• I will leave this up to you. Feel free to use other images of your choosing that wraps around our client.....Activities, Dining, Health, Beauty
Should not have
• just dont be boring

```html
<!DOCTYPE html>
<html lang="en">
<head>
<meta charset="utf-8">
<title>BrightHarborTrade.example – Business Card</title>
<link href="https://fonts.googleapis.com/css2?family=Questrial&display=swap" rel="stylesheet">
<style>
  :root {
    --stage: #3a3a3c;
    --paper: #f7f7f7;
    --blue: #2a87b8;
    --green: #6ab42d;
    --ink-grey: #7b7b7b;
    --ink-dark: #5a5a5a;
  }
  * { margin: 0; padding: 0; box-sizing: border-box; }
  html, body { width: 1200px; height: 834px; overflow: hidden; }
  body {
    background: var(--stage);
    font-family: "Questrial", "Century Gothic", sans-serif;
    position: relative;
  }
  .card {
    position: absolute;
    top: 262px;
    width: 540px;
    height: 309px;
    background: var(--paper);
    overflow: hidden;
    box-shadow: 0 10px 30px rgba(0,0,0,.45);
  }
  .card--front { left: 40px; }
  .card--back { left: 620px; }
  .card svg.card__art { position: absolute; inset: 0; width: 100%; height: 100%; }

  .brand { position: absolute; display: flex; align-items: center; gap: 10px; }
  .brand__dot { width: 28px; height: 28px; border-radius: 50%; background: var(--blue); flex: none; }
  .brand__name { color: var(--green); font-size: 22px; line-height: 1; white-space: nowrap; }
  .brand__tagline { color: var(--ink-dark); font-size: 11px; letter-spacing: .5px; margin-top: 5px; white-space: nowrap; }

  .card--front .brand { left: 48px; top: 98px; }

  .partner { position: absolute; right: 24px; top: 18px; display: flex; flex-direction: column; align-items: center; gap: 5px; }
  .partner__mark { width: 46px; height: 46px; border-radius: 50%; background: var(--green); }
  .partner__name { color: var(--green); font-size: 11px; white-space: nowrap; }

  .card--back .brand { left: 140px; top: 74px; }
  .card--back .brand__name { font-size: 18px; }
  .card--back .brand__dot { width: 24px; height: 24px; }
  .card--back .brand__tagline { font-size: 9px; }

  .contact { position: absolute; left: 36px; top: 142px; }
  .contact__name { color: var(--blue); font-size: 16px; letter-spacing: .5px; }
  .contact__role { color: var(--green); font-size: 12px; margin-bottom: 8px; }
  .contact__address { color: var(--ink-grey); font-size: 10px; line-height: 1.45; margin-bottom: 6px; }
  .contact__list { list-style: none; }
  .contact__item { display: flex; align-items: center; gap: 8px; color: var(--ink-grey); font-size: 10px; line-height: 1.7; }
  .contact__item svg { width: 11px; height: 11px; flex: none; }
</style>
</head>
<body>

<section class="card card--front" aria-label="Card front">
  <svg class="card__art" viewBox="0 0 540 309" preserveAspectRatio="none" aria-hidden="true">
    <path d="M0 272 C170 272 270 262 340 200 C410 138 460 122 540 118 L540 124 C462 128 414 144 345 206 C274 268 170 278 0 278 Z" fill="var(--green)"/>
    <path d="M0 283 C175 283 280 272 350 212 C418 152 466 134 540 130 L540 309 L0 309 Z" fill="var(--blue)"/>
  </svg>
  <div class="partner">
    <div class="partner__mark"></div>
    <div class="partner__name">Amber Ledge Partners</div>
  </div>
  <div class="brand">
    <div class="brand__dot"></div>
    <div>
      <div class="brand__name">BrightHarborTrade.example</div>
      <div class="brand__tagline">Activities-Dining-Health-Beauty</div>
    </div>
  </div>
</section>

<section class="card card--back" aria-label="Card back">
  <svg class="card__art" viewBox="0 0 540 309" preserveAspectRatio="none" aria-hidden="true">
    <path d="M405 0 L540 0 L540 309 L468 309 C482 200 470 90 405 0 Z" fill="var(--green)"/>
    <path d="M378 0 L402 0 C460 75 478 170 466 262 C452 160 430 75 378 0 Z" fill="var(--blue)" stroke="#ffffff" stroke-width="2"/>
  </svg>
  <div class="brand">
    <div class="brand__dot"></div>
    <div>
      <div class="brand__name">BrightHarborTrade.example</div>
      <div class="brand__tagline">Activities-Dining-Health-Beauty</div>
    </div>
  </div>
  <div class="contact">
    <div class="contact__name">DARA WHITLOW</div>
    <div class="contact__role">President</div>
    <div class="contact__address">4870 West 63rd Avenue, Suite C207<br>Phoenix AZ 85731</div>
    <ul class="contact__list">
      <li class="contact__item">
        <svg viewBox="0 0 12 12"><path d="M3 1 L5 3.5 L4 5 C4.8 6.6 5.6 7.4 7 8 L8.5 7 L11 9 L9.5 11 C5 10.5 1.5 7 1 2.5 Z" fill="var(--green)"/></svg>
        555-014-2290
      </li>
      <li class="contact__item">
        <svg viewBox="0 0 12 12"><rect x="1" y="2.5" width="10" height="7" fill="none" stroke="var(--green)" stroke-width="1.2"/><path d="M1 2.5 L6 6.5 L11 2.5" fill="none" stroke="var(--green)" stroke-width="1.2"/></svg>
        dara@brightharbortrade.example
      </li>
      <li class="contact__item">
        <svg viewBox="0 0 12 12"><circle cx="6" cy="6" r="5" fill="none" stroke="var(--green)" stroke-width="1.2"/><ellipse cx="6" cy="6" rx="2.2" ry="5" fill="none" stroke="var(--green)" stroke-width="1"/><path d="M1 6 H11" stroke="var(--green)" stroke-width="1"/></svg>
        www.brightharbortrade.example
      </li>
    </ul>
  </div>
</section>

</body>
</html>
```